Verpackungen Geschenkbox
Eine völlig unkomplizierte und tolle Zusammenarbeit. Und ein ganz tolles Ergebnis. Vielen Dank auch hier noch einmal : )
Zielgruppe
In unserem Studio können Kunden Keramik bemalen
Aufgabenstellung
Ich hätte gerne eine Vorlage für einen Aufkleber, den ich auf eine Verschenkbox machen kann. Diese Geschenkbox werde ich mit einer Rohkeramik füllen, zusätzlich alle Materialien die dafür benötigt werden, wie z.B. Glasuren, Pinsel etc. Diese Boxen sind fertig gerichtet, können direkt gekauft werden und die bemalte Keramik uns wieder zum Brennen gebracht werden. Der Aufkleber dazu soll zu unserem ganzen Stil passen und es soll unser Logo enthalten sein. Es soll zum Kaufen annimieren, aber nicht übertrieben sein. Eher klar auch in den Farben.
Der Aufkleber sollte max. 10 cm groß sein. Der Karton ist viereckig, unterschiedlich groß, so dass eine Tasse, Müslischale oder Teller reinpasst, mit ein paar kleine Fabdosen, Pinsel und anderes Materialien wie Schwamm oder Punktewerkzeug. Achtung, es ist keine Töpferei

```html
<!DOCTYPE html>
<html lang="de">
<head>
<meta charset="utf-8">
<title>Keramikmal-Box – Aufkleber</title>
<link href="https://fonts.googleapis.com/css2?family=Noto+Serif:wght@400;700&family=Kalam:wght@400&display=swap" rel="stylesheet">
<style>
  :root {
    --page: #ecdccf;
    --sticker: #f4f2ee;
    --title: #5b2a26;
    --teal: #1f6d77;
    --sage: #6c7553;
    --slate: #9ba9b6;
    --clay: #b27c60;
  }
  * { margin: 0; padding: 0; box-sizing: border-box; }
  html, body { width: 1200px; height: 800px; overflow: hidden; }
  body {
    background: var(--page);
    display: flex;
    align-items: center;
    justify-content: center;
  }
  .sticker {
    position: relative;
    width: 740px;
    height: 740px;
    background: var(--sticker);
    box-shadow: 0 2px 10px rgba(90, 60, 40, 0.12);
  }
  .brand {
    position: absolute;
    left: 70px;
    top: 56px;
    display: flex;
    align-items: center;
    gap: 12px;
  }
  .brand-dot {
    width: 34px;
    height: 34px;
    border-radius: 50%;
    background: var(--teal);
  }
  .brand-name {
    font-family: "Noto Serif", serif;
    font-weight: 400;
    font-size: 22px;
    letter-spacing: 2px;
    text-transform: uppercase;
    color: var(--teal);
  }
  .title {
    position: absolute;
    left: 66px;
    top: 118px;
    font-family: "Noto Serif", serif;
    font-weight: 700;
    font-size: 68px;
    line-height: 1;
    letter-spacing: 1px;
    white-space: nowrap;
    color: var(--title);
  }
  .tagline {
    position: absolute;
    left: 150px;
    top: 202px;
    font-family: "Kalam", cursive;
    font-size: 28px;
    line-height: 1.2;
    white-space: nowrap;
    color: var(--teal);
  }
  .blob { position: absolute; }
  .blob-clay { left: 470px; top: 280px; width: 200px; height: 160px; }
  .blob-slate { left: 270px; top: 385px; width: 185px; height: 165px; }
  .blob-sage { left: 70px; top: 475px; width: 175px; height: 180px; }
  .contents {
    position: absolute;
    right: 60px;
    top: 590px;
    font-family: "Kalam", cursive;
    font-size: 28px;
    line-height: 1.2;
    white-space: nowrap;
    color: var(--teal);
  }
  .web {
    position: absolute;
    right: 60px;
    top: 648px;
    font-family: "Noto Serif", serif;
    font-size: 22px;
    line-height: 1.2;
    white-space: nowrap;
    color: var(--title);
  }
</style>
</head>
<body>
  <main class="sticker">
    <div class="brand">
      <span class="brand-dot"></span>
      <span class="brand-name">Glasurstube</span>
    </div>
    <h1 class="title">Keramikmal-Box</h1>
    <p class="tagline">für kreative Momente zuhause</p>

    <svg class="blob blob-clay" viewBox="0 0 200 160" role="img" aria-label="Terrakottafarbene Fläche mit Strichzeichnung einer Hand, die mit einem Pinsel malt">
      <path d="M20 70 C10 30 60 5 110 8 C160 10 195 40 192 85 C190 125 150 150 105 148 C60 146 28 115 20 70 Z" fill="var(--clay)"/>
    </svg>
    <svg class="blob blob-slate" viewBox="0 0 185 165" role="img" aria-label="Blaugraue Fläche mit Strichzeichnung von Händen, die eine Schale halten">
      <path d="M15 75 C5 30 50 5 100 8 C150 12 182 45 178 95 C174 140 130 160 85 156 C40 152 22 115 15 75 Z" fill="var(--slate)"/>
    </svg>
    <svg class="blob blob-sage" viewBox="0 0 175 180" role="img" aria-label="Olivgrüne Fläche mit Strichzeichnung von Händen, die eine Tasse halten">
      <path d="M10 60 C15 20 60 0 110 10 C155 20 172 70 168 120 C164 165 120 180 75 172 C30 164 5 110 10 60 Z" fill="var(--sage)"/>
    </svg>

    <p class="contents">Rohkeramik + Farben + Zubehör</p>
    <p class="web">www.glasurstube.de</p>
  </main>
</body>
</html>
```